"Tomi" - Movie Poster for Japanese Black and White Feature Film

We are re-editing and grading an obscure Japanese language film. The film was shot on 35mm quite a few years ago. We have a number of colour stills from the movie. The movies title TOMI is currently being hand drawn by a Japanese artist and will be available shortly. It is mystery drama that cuts between modern and not so modern Japan.
It is not a Japanese horror film, but is plays a little bit spooky in parts. The main character is a writer. He is suffering from writers block. He drinks heavily and fades in and out of his own story to the point where the lines are quite blurred.
Title in Japanese - Guide Text has been uploaded.
狂
華
We are looking for a designer to produce the key art / movie poster. At this stage we are open to all design ideas, although we would like the title to run large down the poster somewhere. The poster will be used on the movies website, along with QRTL and ZPW. Although there will not be a theatrical release, we will be doing a limited addition run of the actual poster. We have attached a number of low quality stills to get this project started. Additional format variations based on the original poster design may also be required.
Once this project has been completed we will require additional work for another title releases. So would be ideally looking for a designer who is interested in creating a distinctive key art style over a slow series of releases.
Any questions, please let me know.
Thank you. Sayaka.
Reason: Working through remaining design submissions.
Thank you.
Reason: We just need a little more time to finalise the text / typography.
Thank you for your patience.
Reason: Finishing up now.

```html
<!DOCTYPE html>
<html lang="en">
<head>
<meta charset="utf-8">
<title>狂華 — Key Art</title>
<link rel="stylesheet" href="https://fonts.googleapis.com/css2?family=Montserrat:wght@400;500&family=Oswald:wght@500;600&family=Yusei+Magic&display=swap">
<style>
  :root {
    --ink: #0b0a09;
    --night: #121312;
    --street: #1e211c;
    --amber: #e8870f;
    --paper: #f1ece4;
  }
  * { margin: 0; padding: 0; box-sizing: border-box; }
  html, body { width: 805px; height: 1200px; overflow: hidden; background: var(--ink); }
  .poster {
    position: relative;
    width: 805px;
    height: 1200px;
    background: linear-gradient(180deg, #0a0908 0%, #0c0b0a 55%, var(--night) 70%);
    overflow: hidden;
  }
  .night-street {
    position: absolute;
    left: 0; right: 0; bottom: 0;
    height: 470px;
    background:
      radial-gradient(ellipse 150px 70px at 130px 205px, rgba(201,160,96,0.45), transparent 75%),
      radial-gradient(ellipse 260px 60px at 500px 200px, rgba(120,110,80,0.18), transparent 80%),
      linear-gradient(180deg, rgba(12,11,10,0) 0%, var(--street) 40%, #171915 60%, #0e0f0d 100%);
  }
  .studio {
    position: absolute;
    top: 47px; left: 0; right: 0;
    text-align: center;
    font-family: "Montserrat", sans-serif;
    font-weight: 500;
    font-size: 16px;
    letter-spacing: 0.42em;
    color: var(--amber);
  }
  .tagline {
    position: absolute;
    top: 78px; left: 0; right: 0;
    text-align: center;
    font-family: "Montserrat", sans-serif;
    font-size: 10.5px;
    line-height: 15px;
    letter-spacing: 0.17em;
    color: var(--paper);
  }
  .title {
    position: absolute;
    top: 310px; left: 0; right: 0;
    margin: 0 auto;
    width: 150px;
    height: 310px;
    writing-mode: vertical-rl;
    text-align: center;
    font-family: "Yusei Magic", sans-serif;
    font-weight: 400;
    font-size: 128px;
    line-height: 150px;
    letter-spacing: 0.1em;
    color: var(--amber);
  }
  .credit {
    position: absolute;
    top: 811px;
    width: 260px;
    text-align: center;
  }
  .credit--writer { left: 71px; }
  .credit--director { left: 483px; }
  .credit__role {
    display: block;
    font-family: "Oswald", sans-serif;
    font-weight: 600;
    font-size: 10px;
    letter-spacing: 0.04em;
    color: var(--paper);
  }
  .credit__name {
    display: block;
    margin-top: 4px;
    font-family: "Montserrat", sans-serif;
    font-weight: 500;
    font-size: 16px;
    letter-spacing: 0.14em;
    color: var(--amber);
  }
</style>
</head>
<body>
  <main class="poster">
    <div class="night-street" role="img" aria-label="Night photograph of a quiet Japanese street with a lit shopfront, railway tracks and low barriers"></div>

    <p class="studio">A NOVAREEL PRODUCTION</p>
    <p class="tagline">BRIGHT, SHARP IMAGES WEAVE A FRAGMENTED DAYDREAM OF FEAR, VIOLENCE AND LOVE LOST,<br>TOLD FROM SEVERAL POINTS OF VIEW.</p>

    <h1 class="title" lang="ja">狂華</h1>

    <div class="credit credit--writer">
      <span class="credit__role">WRITER - PRODUCER</span>
      <span class="credit__name">SAYAKA ISHIDA</span>
    </div>
    <div class="credit credit--director">
      <span class="credit__role">DIRECTOR</span>
      <span class="credit__name">ROWAN HALE</span>
    </div>
  </main>
</body>
</html>
```